Professional and Fun Business Cards for #1 Lagoon Care

We want an updated look for our existing business cards. In addition, we need to update the logos on the back side of the card to be the most current award for Tovey's Index. I have an eps of the Tovey's Index award logo but it is too big to upload here, so I can email it to the designer once selected.

Target Market(s)

Families with swimming pools

Industry/Entity Type

Business

Contact Information for Business Card

Martin Dobrev
Partner & Senior Pool Technician
Dobrev & Kin Pool Service, Inc.
2480 Larkhaven Drive, Suite 312
Roseville, CA 95874
(916) 555-0143 service
(916) 555-0187 billing
info@dobrev-kin.example
www.dobrev-kin.example

Font styles to use
Other font styles liked:
• Goudy Sans Bold

Colors
3176b5
34a7d8
34b8a4
add136

Requirements
Must have
• Dobrev & Kin logo and contact information on the front
• All other logos on the back
Nice to have
• Open to ideas...
Should not have
• Can't think of anything specific

```html
<!DOCTYPE html>
<html lang="en">
<head>
<meta charset="utf-8">
<title>Dobrev &amp; Kin Pool Service – Business Cards</title>
<link rel="stylesheet" href="https://fonts.googleapis.com/css2?family=Alegreya+Sans:wght@700;800&display=swap">
<style>
  :root{
    --page:#e9e6e1;
    --ink-black:#0b0b0d;
    --pool-blue:#3176b5;
    --sky-blue:#34a7d8;
    --deep-blue:#1f5fa3;
    --white:#ffffff;
    --logo-blue:#4aa3e0;
    --badge-gold:#d9c23a;
    --badge-green:#34b8a4;
    --badge-blue:#6aa6dd;
  }
  *{box-sizing:border-box;margin:0;padding:0}
  html,body{width:1200px;height:885px;overflow:hidden;background:var(--page)}
  body{font-family:"Alegreya Sans",sans-serif;font-weight:700;color:var(--white);position:relative}

  .card{
    position:absolute;top:150px;width:350px;height:585px;border-radius:26px;overflow:hidden;
    background:linear-gradient(180deg,var(--sky-blue) 0%,var(--pool-blue) 55%,var(--deep-blue) 100%);
    box-shadow:0 14px 30px rgba(0,0,0,.25);
  }
  .card--back{left:190px}
  .card--front{left:660px}

  .card__header{height:150px;background:var(--ink-black);display:flex;align-items:center;justify-content:center;gap:10px}
  .card__divider{height:6px;background:var(--white);opacity:.9}

  .logo-name{font-size:34px;color:var(--logo-blue);letter-spacing:.5px}
  .logo-mark{width:26px;height:26px;background:var(--logo-blue)}

  .company{font-size:23px;text-align:center;margin-top:22px;letter-spacing:.3px}

  .badges{display:flex;justify-content:center;gap:50px;margin-top:30px}
  .badge{width:62px;height:62px;border-radius:50%}
  .badge--award{background:var(--badge-gold);box-shadow:0 0 0 5px var(--badge-green)}
  .badge--cert{background:var(--badge-blue);box-shadow:0 0 0 4px var(--white)}

  .splash{position:absolute;left:0;right:0;bottom:0;height:300px}

  .person{text-align:center;margin-top:30px}
  .person__name{font-size:24px}
  .person__role{font-size:16px;margin-top:2px}

  .contact{list-style:none;text-align:center;margin-top:40px}
  .contact li{display:flex;flex-direction:column;align-items:center;font-size:17px;margin-bottom:8px}
  .contact svg{width:18px;height:16px;margin-bottom:2px}
  .contact .address{font-size:16px;line-height:1.15}
</style>
</head>
<body>

<section class="card card--back" aria-label="Card back">
  <header class="card__header">
    <span class="logo-mark"></span>
    <span class="logo-name">Dobrev &amp; Kin</span>
  </header>
  <div class="card__divider"></div>
  <p class="company">Dobrev &amp; Kin Pool Service, Inc</p>
  <div class="badges">
    <span class="badge badge--award" aria-label="Tovey's Index award badge"></span>
    <span class="badge badge--cert" aria-label="Pool operator certification badge"></span>
  </div>
  <svg class="splash" role="img" aria-label="Photo of white water splash over blue pool" viewBox="0 0 350 300" preserveAspectRatio="none">
    <defs>
      <linearGradient id="splashFill" x1="0" y1="0" x2="1" y2="1">
        <stop offset="0" stop-color="#ffffff" stop-opacity=".9"/>
        <stop offset=".6" stop-color="#cfe6f6" stop-opacity=".6"/>
        <stop offset="1" stop-color="#34a7d8" stop-opacity="0"/>
      </linearGradient>
    </defs>
    <rect width="350" height="300" fill="url(#splashFill)"/>
  </svg>
</section>

<section class="card card--front" aria-label="Card front">
  <header class="card__header">
    <span class="logo-mark"></span>
    <span class="logo-name">Dobrev &amp; Kin</span>
  </header>
  <div class="card__divider"></div>
  <p class="company">Dobrev &amp; Kin Pool Service, Inc</p>
  <div class="person">
    <p class="person__name">Martin Dobrev</p>
    <p class="person__role">Partner &amp; Senior Pool Technician</p>
  </div>
  <ul class="contact">
    <li>
      <svg viewBox="0 0 18 16"><path d="M4 1 L7 4 L5 6 Q8 10 12 11 L14 9 L17 12 L15 15 Q5 14 1 4 Z" fill="#fff"/></svg>
      (916) 555-0143
    </li>
    <li>
      <svg viewBox="0 0 18 16"><path d="M4 1 L7 4 L5 6 Q8 10 12 11 L14 9 L17 12 L15 15 Q5 14 1 4 Z" fill="#fff"/></svg>
      (916) 555-0187
    </li>
    <li>
      <svg viewBox="0 0 18 16"><rect x="1" y="3" width="16" height="11" fill="#fff"/><path d="M1 3 L9 9 L17 3" stroke="#3176b5" stroke-width="1.5" fill="none"/></svg>
      info@dobrev-kin.example
    </li>
    <li>
      <svg viewBox="0 0 18 16"><circle cx="9" cy="8" r="7" fill="none" stroke="#fff" stroke-width="1.6"/><path d="M2 8 H16 M9 1 Q4 8 9 15 M9 1 Q14 8 9 15" stroke="#fff" stroke-width="1.2" fill="none"/></svg>
      www.dobrev-kin.example
    </li>
    <li class="address">
      <svg viewBox="0 0 18 16"><path d="M9 15 Q3 8 3 6 A6 6 0 0 1 15 6 Q15 8 9 15 Z" fill="#fff"/><circle cx="9" cy="6" r="2" fill="#3176b5"/></svg>
      2480 Larkhaven Drive, Suite 312 Roseville<br>CA 95874
    </li>
  </ul>
</section>

</body>
</html>
```